New Book and ebook Cover Design healing holistic/integrative cancer Project

Creation of an Ebook + Book format A5. about cure of Cancer.

Guide d'aide à la guérison

Under title Développez vos capacités de "guérisseur intérieur"
Créez votre résiliance, transmutez votre maladie en cadeaux de la vie.
Develop your self healer skills: Create your resilience, transmute your illness into gifts of life.

The 3 mains idea for the book:
- A symbolic with the icone pink of cancer with french word around (like: amour, aide, guérison, holistique, âme, corps, esprit, divin, vie):
The main target is people with cancer
Image of cancer icon ot with a tree;
- Create a Healing Journey ( image included or another idea)
- A tranversal integrative (global health soul body spirit )Journey Trough :
Spirituality, the psychoemotionnel understanding of the disease, the benefits of row ecologic foods, the medecines of the word, (Ayurveda, Chinese, Shamanism), quantum medicine, energy healing,+16 auto techniques self care
So you can illustrate the main parcours with image or icon about it
readers must feel the love the main what this book can bring them as gifts

Additionnal icon :
l’icône Leafward Pledge blue can be added. Promesse Leafward

Target Market(s)

people with cancer, professionnel of healing in integrative issue

Industry/Entity Type

Health And Wellness

Other font styles liked:
• arial colibri

Colors
abd037
e667a6
a64599

Requirements
Must have
• The 3 mains idea for the book:
• - A symbolic with the icone pink of cancer with french word around (like: amour, aide, guérison, holistique, âme, corps, esprit, divin, vie):
• The main target is people with cancer
• Image of cancer icon ot with a tree;
• - Create a Healing Journey ( image included or another idea)
• - A tranversal integrative (global health soul body spirit )Journey Trough :
• Spirituality, the psychoemotionnel understanding of the disease, the benefits of row ecologic foods, the medecines of the word, (Ayurveda, Chinese, Shamanism), quantum medicine, energy healing,+16 auto techniques self care
• So you can illustrate the main parcours with image or icon about it
• readers must feel the love the main what this book can bring them as gifts
• If you don't put icone or image for the benefits about the book:
• cloud of words in cancer symbol (and replace love words by this list)
• Parcours de Guérisons : Create a Healing Journey
• Médecine Intégrative -Santé Intégrative (âme-corps-esprit) (Soul-Body-Spirit)
• Médecine du Monde (Ayurveda, Médecine Chinoise, Chamanisme) ( Ayurveda, Chinese Médicine, Shamanism)
• Alimentation vibrante ( vibrant raw food)
• Energies de guérison
• Plus de 20 Techniques d’auto-soins
Nice to have
• 1/idea of ​​backgrounds with orbs in violet color (the fine notion of connection to the universe to the divine is to be passed on in this book)
• 2/ People can Create their own Healing Journey '( image for healing journey with roads for exemple)
• 3/ cancer symbole with words around spirit of the book french word around (like: amour, aide, guérison, holistique, âme, corps, esprit, divin, vie):
• pink/magenta and green color
• 4/ idea of gift with love?
• 5/ Lucien Marvaux ( Name of autor)
• The goal is you can live, it's possible!
Should not have
• put to much information keep focuse on the spirit of the book. People in less 30 second will be interest for buy and USED this book
• use the same type of the same type of font

```html
<!DOCTYPE html>
<html lang="fr">
<head>
<meta charset="utf-8">
<title>Quatrième de couverture – Guide d'aide à la guérison</title>
<link href="https://fonts.googleapis.com/css2?family=Carlito:wght@400;700&display=swap" rel="stylesheet">
<style>
  :root {
    --sky-top: #7fa6e6;
    --sky-mid: #c9e2f8;
    --sky-light: #f3f8fd;
    --glow: #ffffff;
    --grass-light: #b7d97a;
    --grass: #6fae3a;
    --grass-deep: #4c8d2a;
    --headline: #d84f98;
    --panel: #c64587;
    --panel-text: #ffffff;
    --body-text: #1d1d1f;
    --photo-top: #e4e7ee;
    --photo-bottom: #2f3a4f;
    --ornament: #b89a72;
  }
  * { margin: 0; padding: 0; box-sizing: border-box; }
  html, body { width: 880px; height: 1200px; overflow: hidden; }
  body { font-family: "Carlito", "Calibri", sans-serif; color: var(--body-text); }

  .back-cover {
    position: relative;
    width: 880px;
    height: 1200px;
    overflow: hidden;
    background:
      radial-gradient(circle at 14% 12%, var(--glow) 0, rgba(255,255,255,0.9) 9%, rgba(255,255,255,0) 34%),
      radial-gradient(ellipse at 50% 60%, var(--sky-light) 0, rgba(243,248,253,0.9) 40%, rgba(243,248,253,0) 75%),
      linear-gradient(180deg, var(--sky-top) 0%, var(--sky-mid) 30%, var(--sky-light) 65%, #eef6ea 82%);
  }

  .meadow {
    position: absolute;
    left: 0; right: 0; bottom: 0;
    height: 210px;
    background: linear-gradient(180deg, rgba(183,217,122,0) 0%, var(--grass-light) 22%, var(--grass) 55%, var(--grass-deep) 100%);
  }

  .sacred-emblem {
    position: absolute;
    left: 332px; top: 22px;
    width: 220px; height: 220px;
  }

  .headline {
    position: absolute;
    top: 286px; left: 60px; width: 760px;
    text-align: center;
    color: var(--headline);
    font-weight: 700;
    font-size: 21.5px;
    line-height: 24px;
    letter-spacing: 0.2px;
    text-transform: uppercase;
  }

  .blurb {
    position: absolute;
    top: 368px; left: 92px; width: 696px;
    text-align: center;
    font-size: 17.4px;
    line-height: 23.6px;
  }
  .blurb p + p { margin-top: 23.6px; }

  .author-panel {
    position: absolute;
    left: 83px; top: 804px;
    width: 720px; height: 260px;
    background: var(--panel);
    color: var(--panel-text);
  }
  .author-photo {
    position: absolute;
    left: 0; bottom: 0;
    width: 213px; height: 252px;
    background: linear-gradient(180deg, var(--photo-top) 0%, #c7ccd6 45%, var(--photo-bottom) 100%);
  }
  .author-bio {
    position: absolute;
    left: 237px; top: 20px; width: 475px;
    font-size: 15.7px;
    line-height: 21.8px;
  }
</style>
</head>
<body>
  <main class="back-cover">
    <div class="meadow" role="img" aria-label="Prairie verte fleurie sous le ciel"></div>

    <svg class="sacred-emblem" viewBox="0 0 220 220" role="img" aria-label="Motif de fleur de vie doré entouré de rayons de lumière">
      <defs>
        <radialGradient id="emblemGlow" cx="50%" cy="50%" r="50%">
          <stop offset="0%" stop-color="#fff8ec" stop-opacity="0.75"/>
          <stop offset="100%" stop-color="#e9dcc6" stop-opacity="0.35"/>
        </radialGradient>
      </defs>
      <circle cx="110" cy="110" r="108" fill="url(#emblemGlow)" stroke="var(--ornament)" stroke-width="1.5"/>
    </svg>

    <h1 class="headline">Et si votre maladie n’était autre que l’appel de<br>votre âme à retrouver votre essence véritable ?</h1>

    <section class="blurb">
      <p>Cet ouvrage est une invitation à entreprendre l’alchimie en vous grâce à l’Amour.</p>
      <p>Un chemin de guérison est et reste plus que jamais possible. Empreinte de sagesse Divine, la spiritualité est décryptée avec simplicité en y associant une compréhension globale de l’être âme corps esprit dans un recouvrement intégratif de la guérison. Vous y découvrirez une mine d’informations utiles pour vous aider à transmuter votre plomb en or.</p>
      <p>Concentré d’outils tant Ancestraux que modernes allant de l’Alimentation Saine Vivante et Vibrante, la Respiration Consciente, l’Aromathérapie, l’EFT, l’Auto-hypnose Humaniste, la Lithothérapie, la Musicothérapie, la Réflexologie Plantaire… aux Médecines millénaires du monde sans oublier les possibilités offertes par les thérapies Quantiques dans une dimension énergétique multidimensionnelle de l’être.</p>
    </section>

    <aside class="author-panel">
      <div class="author-photo" role="img" aria-label="Portrait de l’auteur en veste sombre et chemise claire"></div>
      <p class="author-bio">LUCIEN MARVAUX, formé à la santé de l’Habitat avec le Feng Shui Traditionnel Chinois et la Géobiologie et différents outils de santé holistique allant de l’Aromathérapie aux Thérapies Quantiques. L’écriture de ce livre lui est apparue comme un appel du cœur désireux d’apporter une aide significative pour prévenir et aider à traiter le cancer ou toutes autres maladies différemment sous un angle intégratif âme-corps-esprit sans rejeter la médecine conventionnelle, mais l’inclure dans une réalité plus vaste.</p>
    </aside>
  </main>
</body>
</html>
```